Church Christmas Flyer

The flyer is to advertise our Christmas Eve services. The flyer is for a Christian church service to celebrate the birth of Jesus. We would like to see designs that use blue, silver and gold for colors but feel free to be creative. We are interested in a flyer that is has texture, depth and is more abstract than literal. Don't be afraid to layer. Please make the flyer double sided

* I uploaded our Christmas flyer from last year.

Target Market(s)

30-55 year old, male and female

Industry/Entity Type

Church

Requirements
Must have
• Map to the church
Church phone number 555-316-0479
Service times 3:00pm and 5:00pm
church address 2083 Marlow Ave, Hesperia, Ca. 92351
church website www.brookfieldfellowship.example
Scripture verse

Text must stand out and be easy to read
Nice to have
• Use of the star in the sky that guided the wise men to Jesus.
Should not have
• Santa Clause, Snowmen, Reindeer

```html
<!DOCTYPE html>
<html lang="en">
<head>
<meta charset="utf-8">
<title>Brookfield Fellowship – Christmas Eve</title>
<link rel="stylesheet" href="https://fonts.googleapis.com/css2?family=Questrial&family=Pinyon+Script&display=swap">
<style>
  :root {
    --ink: #000000;
    --night: #050a18;
    --deep-blue: #0d2a6e;
    --sky-blue: #1f4fb0;
    --teal: #2c6f78;
    --gold: #e6a81c;
    --gold-soft: #f2c24a;
    --white: #ffffff;
    --silver: #9aa0a8;
    --verse-blue: #3f7fd6;
    --verse-teal: #5fb7c4;
    --verse-pale: #a9d8ee;
    --map-tone: #cfe0f0;
  }
  * { margin: 0; padding: 0; box-sizing: border-box; }
  html, body { width: 1200px; height: 1097px; overflow: hidden; background: var(--ink); }
  body { position: relative; font-family: "Questrial", "Century Gothic", sans-serif; color: var(--white); }

  .side { position: absolute; left: 0; width: 1200px; overflow: hidden; }
  .side--front { top: 0; height: 548px; }
  .side--back { top: 548px; height: 549px; }

  .scene { position: absolute; top: 0; height: 100%; }
  .side--front .scene {
    left: 0; width: 1120px;
    background:
      radial-gradient(ellipse 420px 200px at 260px 70px, rgba(40,90,200,.85), transparent 70%),
      radial-gradient(ellipse 300px 160px at 1020px 60px, rgba(200,150,40,.45), transparent 70%),
      linear-gradient(180deg, var(--deep-blue) 0%, var(--night) 45%, #0b1a22 70%, var(--teal) 100%);
  }
  .side--front .edge { position: absolute; right: 0; top: 0; width: 80px; height: 100%; background: var(--ink); }
  .side--back .scene {
    left: 60px; width: 1140px;
    background:
      radial-gradient(ellipse 360px 200px at 1000px 60px, rgba(40,90,200,.9), transparent 70%),
      radial-gradient(ellipse 260px 140px at 140px 70px, rgba(220,160,40,.55), transparent 70%),
      radial-gradient(ellipse 380px 140px at 260px 420px, rgba(200,170,110,.35), transparent 70%),
      linear-gradient(180deg, #0a1a40 0%, var(--night) 40%, #10151e 75%, #232a33 100%);
  }
  .star { position: absolute; width: 6px; height: 6px; border-radius: 50%; background: var(--white); box-shadow: 0 0 10px 4px rgba(255,255,255,.7); }

  .t { position: absolute; white-space: nowrap; line-height: 1; }
  .right { text-align: right; }

  .church-name { right: 105px; top: 64px; font-size: 52px; color: var(--gold); text-shadow: 0 2px 6px rgba(0,0,0,.6); }
  .site-small { left: 395px; top: 127px; font-size: 17px; color: #d8d8d8; }
  .event-title { right: 105px; top: 135px; font-size: 52px; }
  .event-sub { right: 105px; top: 192px; font-size: 30px; }

  .verse { font-family: "Pinyon Script", cursive; font-size: 38px; color: var(--white); }
  .verse-1 { right: 70px; top: 290px; }
  .verse-2 { left: 70px; top: 360px; }
  .verse-3 { right: 70px; top: 430px; }
  .verse .hl { font-size: 58px; }
  .hl--mighty { color: var(--verse-blue); }
  .hl--delight { color: var(--verse-teal); }
  .hl--love { color: var(--white); }
  .hl--rejoice, .hl--singing { color: var(--verse-pale); }
  .verse-ref { left: 810px; top: 492px; font-size: 18px; color: #c8c8c8; }

  .service-title { left: 82px; top: 634px; font-size: 50px; }
  .service-sub { left: 88px; top: 684px; font-size: 30px; }
  .service-date { left: 150px; top: 762px; font-size: 80px; color: var(--gold); }
  .service-times { left: 345px; top: 862px; font-size: 52px; color: var(--gold); }
  .back-name { left: 90px; top: 978px; font-size: 44px; color: var(--silver); text-shadow: 0 2px 4px rgba(0,0,0,.8); }
  .back-address { left: 90px; top: 1028px; font-size: 32px; color: #d0d0d0; }
  .back-site { left: 842px; top: 993px; font-size: 21px; color: #e6e6e6; }
  .back-phone { left: 900px; top: 1033px; font-size: 32px; }

  .map {
    position: absolute; left: 852px; top: 662px; width: 300px; height: 297px;
    border: 2px solid var(--gold);
    background: linear-gradient(135deg, var(--map-tone), #e8eef4 60%, #c4d8ea);
  }
</style>
</head>
<body>
  <section class="side side--front">
    <div class="scene" role="img" aria-label="Night sky with the guiding star, golden light, a cross on a hill and stone ground, overlaid with faint Christmas Eve script"></div>
    <div class="edge"></div>
    <span class="star" style="left:187px;top:86px"></span>
    <p class="t church-name right">Brookfield Fellowship</p>
    <p class="t site-small">www.brookfieldfellowship.example</p>
    <h1 class="t event-title right">Christmas Eve</h1>
    <p class="t event-sub right">A Celebration of God’s love</p>
    <p class="t verse verse-1">“The Lord your God is with you, he is <span class="hl hl--mighty">mighty</span> to save.</p>
    <p class="t verse verse-2">He will take great <span class="hl hl--delight">delight</span> in you, he will quiet you with his <span class="hl hl--love">love</span>,</p>
    <p class="t verse verse-3">he will <span class="hl hl--rejoice">rejoice</span> over you with <span class="hl hl--singing">singing</span>.”</p>
    <p class="t verse-ref">Zephaniah 3:17</p>
  </section>

  <section class="side side--back">
    <div class="scene" role="img" aria-label="Night sky with the guiding star, golden light streaks and a cross silhouetted at sunset, with faint December script"></div>
    <span class="star" style="left:992px;top:86px"></span>
  </section>

  <h2 class="t service-title">Christmas Eve Service</h2>
  <p class="t service-sub">A Celebration of God’s love</p>
  <p class="t service-date">December 24th</p>
  <p class="t service-times">3:00pm &amp; 5:00pm</p>
  <div class="map" role="img" aria-label="Street map showing the route to the church"></div>
  <p class="t back-name">Brookfield Fellowship</p>
  <p class="t back-address">2083 Marlow Ave, Hesperia, Ca. 92351</p>
  <p class="t back-site">www.brookfieldfellowship.example</p>
  <p class="t back-phone">555-316-0479</p>
</body>
</html>
```